Business Cards Needed for Innovative Healthcare Marketing Company

We are a marketing company focused on healthcare. Our company is all about rebranding yourself renewing your image and generating results. The phoenix stands for "reborn" or "rising" which we provide new brands for our clients we take their old brands and renew it with creativity and innovation. I am looking for a business card with color dimension. I have attached an example of a card I think has the look and feel of what I am trying to accomplish. I like that the card example has black and grey font colors, I like the font placement and the small logo, I really like the use of the colors on the right those are the colors of my logo. My logo is phoenix so maybe incorporating flames similar to that design. I would like the back a solid color maybe red with an opaque version of the logo and website. As a marketing company I am always open to creative liberty!

Target Market(s)

Doctors and business professionals.

Industry/Entity Type

Marketing

Contact Information for Business Card

Valcorne Health Care Marketing
Marla Tenwick- CEO
#(512)638-2974
email-marla@valcorne.com
website- valcorne.com

Font styles to use
Sans Serif

Colors
ec1f27
f37122
ffc214
fbed22
fbf289
f04a50

Requirements
Must have
• The logo and required information
Nice to have
• icons by the information
Should not have
• child like font

```html
<!DOCTYPE html>
<html lang="en">
<head>
<meta charset="utf-8">
<title>Valcorne Health Care Marketing – Business Card</title>
<link rel="stylesheet" href="https://fonts.googleapis.com/css2?family=Questrial&family=Open+Sans:wght@400;700&display=swap">
<style>
  :root {
    --canvas: #e9e6e2;
    --card-black: #0b0b0b;
    --phoenix-shadow: #242424;
    --brand-red: #b2262c;
    --card-red: #a4282e;
    --brand-orange: #f5a01f;
    --flame-orange: #f37122;
    --flame-yellow: #ffc214;
    --ink-dark: #1a1a1a;
    --ink-light: #ffffff;
  }
  * { margin: 0; padding: 0; box-sizing: border-box; }
  html, body {
    width: 1200px; height: 900px; overflow: hidden;
    background: var(--canvas);
  }
  .canvas {
    position: relative; width: 1200px; height: 900px;
  }
  .card {
    position: absolute; left: 280px; width: 640px; height: 366px;
    overflow: hidden;
    box-shadow: 0 6px 18px rgba(0,0,0,0.18);
  }
  .card--back { top: 56px; background: var(--card-black); }
  .card--front { top: 478px; background: var(--card-red); }

  /* Back side */
  .phoenix-decoration {
    position: absolute; left: 20px; top: 10px; width: 290px; height: 346px;
    background: radial-gradient(ellipse at 55% 40%, var(--phoenix-shadow) 0%, rgba(36,36,36,0.6) 45%, rgba(11,11,11,0) 75%);
  }
  .brand {
    position: absolute;
    font-family: "Questrial", sans-serif;
    font-weight: 400;
  }
  .brand__name {
    display: block; letter-spacing: 1px; line-height: 1;
    padding-bottom: 6px; border-bottom: 1px solid currentColor;
  }
  .brand__tagline {
    display: block; letter-spacing: 1.5px; line-height: 1; margin-top: 6px;
  }
  .brand--back {
    left: 268px; top: 104px; color: var(--brand-red);
  }
  .brand--back .brand__name { font-size: 40px; }
  .brand--back .brand__tagline { font-size: 15px; }
  .brand-dot {
    position: absolute; left: 228px; top: 110px;
    width: 30px; height: 30px; border-radius: 50%;
    background: var(--brand-red);
  }

  /* Front side */
  .brand--front {
    left: 118px; top: 168px; color: var(--brand-orange);
  }
  .brand--front .brand__name { font-size: 50px; }
  .brand--front .brand__tagline { font-size: 18px; }

  .person {
    position: absolute; right: 28px; top: 30px; text-align: right;
  }
  .person__name {
    font-family: "Questrial", sans-serif; font-size: 25px;
    color: var(--brand-orange); letter-spacing: 0.5px;
  }
  .person__title {
    font-family: "Open Sans", sans-serif; font-weight: 700; font-size: 13px;
    color: var(--ink-dark); margin-top: 4px; margin-right: 60px;
  }
  .contact {
    position: absolute; left: 450px; top: 200px; list-style: none;
    font-family: "Open Sans", sans-serif; font-size: 13.5px; color: var(--ink-light);
  }
  .contact__item {
    display: flex; align-items: center; gap: 8px; line-height: 20px;
  }
  .contact__icon { width: 12px; height: 12px; flex: none; }
  .flame-border {
    position: absolute; left: 0; bottom: 0; width: 100%; height: 34px;
    background: linear-gradient(to top, var(--flame-orange) 0%, var(--flame-yellow) 70%, rgba(255,194,20,0) 100%);
  }
</style>
</head>
<body>
<main class="canvas">

  <section class="card card--back" aria-label="Card back">
    <div class="phoenix-decoration" role="img" aria-label="Large faint phoenix with spread wings"></div>
    <span class="brand-dot" aria-hidden="true"></span>
    <div class="brand brand--back">
      <span class="brand__name">VALCORNE</span>
      <span class="brand__tagline">HEALTHCARE MARKETING</span>
    </div>
  </section>

  <section class="card card--front" aria-label="Card front">
    <div class="person">
      <p class="person__name">Marla Tenwick</p>
      <p class="person__title">CEO</p>
    </div>

    <div class="brand brand--front">
      <span class="brand__name">VALCORNE</span>
      <span class="brand__tagline">HEALTHCARE MARKETING</span>
    </div>

    <ul class="contact">
      <li class="contact__item">
        <svg class="contact__icon" viewBox="0 0 12 12" aria-hidden="true"><path fill="#fff" d="M1 4c0-2 1-3 5-3s5 1 5 3l-2 1-1-2H4L3 5zM3 6h6l1 5H2z"/></svg>
        <span>(512)638-2974</span>
      </li>
      <li class="contact__item">
        <svg class="contact__icon" viewBox="0 0 12 12" aria-hidden="true"><rect x="0.5" y="2.5" width="11" height="7" fill="#fff"/><path d="M1 3l5 4 5-4" stroke="#a4282e" fill="none"/></svg>
        <span>marla@valcorne.com</span>
      </li>
      <li class="contact__item">
        <svg class="contact__icon" viewBox="0 0 12 12" aria-hidden="true"><circle cx="6" cy="6" r="5.5" fill="#fff"/><path d="M1 6h10M6 .5c-2 2-2 9 0 11M6 .5c2 2 2 9 0 11" stroke="#a4282e" stroke-width="0.8" fill="none"/></svg>
        <span>valcorne.com</span>
      </li>
    </ul>

    <div class="flame-border" role="img" aria-label="Row of small orange and yellow flames along the bottom edge"></div>
  </section>

</main>
</body>
</html>
```